Willow Crest Brand - Bag Design

We are a company dealing with nuts, grains and seeds and are looking for a design for our retail bag packaging that will be consistent across all our product range. We are currently differentiating in way of color but please feel free to be more creative if you wish. Sample of products include pumpkin seeds, rolled oats, almonds, etc.
Design Idea: Hygienic, Natural (from Nature), Quality & Upscale, Simple & Clean design
Target Market: High-end Markets, end-users of A/B type.
1. Bag size is 210 mm (width) * 310 mm (length). Material is OPP or multi-layer PP.
2. Front must have clear window to show packed products. Back clear window is optional.
3. Front side must have logo that stands out (Willow Crest) as attached.
4. Front side must have product name and net weight.
5. Back side must have enough space for Nutrition Fact, product descriptions (110 mm * 100 mm), and barcode.
6. Back side must have white space to print production and expiry dates about 25 mm * 30 mm.
7. Top and bottom of bag must be opaque and not show product.
Reason: Extended period for more new ideas and also for requested modification.
Target Market(s)
Premium market. Type A to B customers as well as professional clients. The product is not a snack. It is for cooking or baking.
Industry/Entity Type
Food Store
Requirements
Must have
- Look unique and stand out from others in the market.
- The colors of the word "Willow Crest" and the blue air-brush in the logo can be changed.
Nice to have
- See project description
Should not have
- See project description

```html
<!DOCTYPE html>
<html lang="en">
<head>
<meta charset="utf-8">
<title>Willow Crest – Retail Bag Range</title>
<link href="https://fonts.googleapis.com/css2?family=Bebas+Neue&family=Montserrat:wght@500;700;800&display=swap" rel="stylesheet">
<style>
  :root {
    --page-bg: #ffffff;
    --paper: #f4f4f4;
    --ink-white: #f7f7f5;
    --brand-blue: #2e3f99;
    --pumpkin-top: #e58a12;
    --pumpkin-bottom: #f2c811;
    --pumpkin-ink: #e9a10f;
    --almond-top: #5e4637;
    --almond-mid: #b56d28;
    --almond-ink: #7a5438;
  }
  html, body {
    margin: 0;
    width: 1200px;
    height: 1200px;
    overflow: hidden;
    background: var(--page-bg);
  }
  .range {
    position: relative;
    width: 1200px;
    height: 1200px;
  }
  .bag {
    position: absolute;
    top: 260px;
    width: 408px;
    height: 604px;
  }
  .bag--pumpkin { left: 88px; }
  .bag--almond { left: 680px; }
  .bag svg { display: block; width: 100%; height: 100%; }
  .tagline {
    font-family: "Montserrat", sans-serif;
    font-weight: 500;
    font-size: 15px;
    letter-spacing: 7px;
    fill: var(--ink-white);
  }
  .brand-name {
    font-family: "Montserrat", sans-serif;
    font-weight: 700;
    font-size: 19px;
    fill: var(--brand-blue);
  }
  .product-name {
    font-family: "Bebas Neue", sans-serif;
    fill: var(--ink-white);
  }
  .net-weight {
    font-family: "Montserrat", sans-serif;
    font-weight: 800;
    font-size: 12px;
    fill: var(--ink-white);
  }
  .badge-disc { fill: var(--ink-white); }
  .badge-text {
    font-family: "Montserrat", sans-serif;
    font-weight: 700;
    font-size: 17px;
    letter-spacing: 1px;
  }
  .bag--pumpkin .badge-text { fill: var(--pumpkin-ink); }
  .bag--almond .badge-text { fill: var(--almond-ink); }
</style>
</head>
<body>
<main class="range">

  <!-- Pumpkin seeds -->
  <section class="bag bag--pumpkin">
    <svg viewBox="0 0 408 604" xmlns="http://www.w3.org/2000/svg">
      <defs>
        <linearGradient id="pumpkin-body" x1="0" y1="0" x2="0" y2="1">
          <stop offset="0" stop-color="var(--pumpkin-top)"/>
          <stop offset="0.55" stop-color="#efaa10"/>
          <stop offset="1" stop-color="var(--pumpkin-bottom)"/>
        </linearGradient>
        <linearGradient id="pumpkin-fill" x1="0" y1="0" x2="1" y2="1">
          <stop offset="0" stop-color="#efe6cf"/>
          <stop offset="1" stop-color="#d9cba6"/>
        </linearGradient>
        <clipPath id="pumpkin-clip"><rect width="408" height="604"/></clipPath>
      </defs>
      <g clip-path="url(#pumpkin-clip)">
        <rect class="bag-body" width="408" height="604" fill="url(#pumpkin-body)"/>
        <polygon class="header-panel" points="52,0 408,0 408,118 52,126" fill="var(--paper)"/>
        <g class="brand-lockup">
          <circle cx="84" cy="82" r="9" fill="var(--brand-blue)"/>
          <text class="brand-name" x="100" y="89">Willow Crest</text>
        </g>
        <text class="tagline" transform="translate(34 356) rotate(-90)">PREMIUM ORGANIC</text>
        <text class="product-name" x="86" y="250" font-size="150" textLength="330" lengthAdjust="spacingAndGlyphs">PUMPKIN</text>
        <text class="product-name" x="94" y="376" font-size="150" textLength="170" lengthAdjust="spacingAndGlyphs">SEEDS</text>
        <g role="img" aria-label="Clear window showing white pumpkin seeds">
          <polygon points="30,426 70,410 110,396 160,392 200,384 240,380 290,376 340,366 380,364 408,360 408,430 360,438 320,452 270,460 220,468 170,474 120,480 80,482 40,486 30,480"
                   fill="url(#pumpkin-fill)"/>
        </g>
        <text class="net-weight" x="88" y="576">200G</text>
        <circle class="badge-disc" cx="176" cy="570" r="36"/>
        <text class="badge-text" x="176" y="566" text-anchor="middle">HEA</text>
        <text class="badge-text" x="176" y="584" text-anchor="middle">LTHY</text>
        <circle class="badge-disc" cx="264" cy="566" r="36"/>
        <text class="badge-text" x="264" y="562" text-anchor="middle">NAT</text>
        <text class="badge-text" x="264" y="580" text-anchor="middle">URAL</text>
        <circle class="badge-disc" cx="350" cy="562" r="36"/>
        <text class="badge-text" x="350" y="558" text-anchor="middle">ORG</text>
        <text class="badge-text" x="350" y="576" text-anchor="middle">ANIC</text>
      </g>
    </svg>
  </section>

  <!-- Natural almonds -->
  <section class="bag bag--almond">
    <svg viewBox="0 0 408 604" xmlns="http://www.w3.org/2000/svg">
      <defs>
        <linearGradient id="almond-body" x1="0" y1="0" x2="0" y2="1">
          <stop offset="0" stop-color="var(--almond-top)"/>
          <stop offset="0.6" stop-color="var(--almond-mid)"/>
          <stop offset="1" stop-color="#8a5a34"/>
        </linearGradient>
        <linearGradient id="almond-fill" x1="0" y1="0" x2="1" y2="1">
          <stop offset="0" stop-color="#c07a45"/>
          <stop offset="1" stop-color="#8f5228"/>
        </linearGradient>
        <clipPath id="almond-clip"><rect width="408" height="604"/></clipPath>
      </defs>
      <g clip-path="url(#almond-clip)">
        <rect class="bag-body" width="408" height="604" fill="url(#almond-body)"/>
        <polygon class="header-panel" points="52,0 408,0 408,118 52,126" fill="var(--paper)"/>
        <g class="brand-lockup">
          <circle cx="84" cy="82" r="9" fill="var(--brand-blue)"/>
          <text class="brand-name" x="100" y="89">Willow Crest</text>
        </g>
        <text class="tagline" transform="translate(34 356) rotate(-90)">PREMIUM ORGANIC</text>
        <text class="product-name" x="70" y="250" font-size="150" textLength="320" lengthAdjust="spacingAndGlyphs">NATURAL</text>
        <text class="product-name" x="78" y="376" font-size="150" textLength="314" lengthAdjust="spacingAndGlyphs">ALMONDS</text>
        <g role="img" aria-label="Clear window showing whole natural almonds">
          <polygon points="30,426 70,410 110,396 160,392 200,384 240,380 290,376 340,366 380,364 408,360 408,430 360,438 320,452 270,460 220,468 170,474 120,480 80,482 40,486 30,480"
                   fill="url(#almond-fill)"/>
        </g>
        <text class="net-weight" x="88" y="576">200G</text>
        <circle class="badge-disc" cx="176" cy="570" r="36"/>
        <text class="badge-text" x="176" y="566" text-anchor="middle">HEA</text>
        <text class="badge-text" x="176" y="584" text-anchor="middle">LTHY</text>
        <circle class="badge-disc" cx="264" cy="566" r="36"/>
        <text class="badge-text" x="264" y="562" text-anchor="middle">NAT</text>
        <text class="badge-text" x="264" y="580" text-anchor="middle">URAL</text>
        <circle class="badge-disc" cx="350" cy="562" r="36"/>
        <text class="badge-text" x="350" y="558" text-anchor="middle">ORG</text>
        <text class="badge-text" x="350" y="576" text-anchor="middle">ANIC</text>
      </g>
    </svg>
  </section>

</main>
</body>
</html>
```